Logo, Web and Mobile Designs for enterprise social media platform

All the details are in the attached document, please start reading the scope document first which explains what is this project about and the details about the needed deliverables, after that please read the UI_Requirements document which will detail what is expected regarding the coded web version since this is a coded contest, it is very important that you meet the UI requirements or suggest something else but we will need to agree first before working on the coded version

Good Luck

Target Market(s)

Enterprise Social Media

Industry/Entity Type

Media

Coding

Coded - Design and coding required

Number of Pages Required

5+ page

Font styles to use
Sans Serif

Requirements
Must have
• All the must haves are listed in the scope document so please check before you start

```html
<!DOCTYPE html>
<html lang="en">
<head>
<meta charset="utf-8">
<title>Teamora – Create New Business Opportunity</title>
<link href="https://fonts.googleapis.com/css2?family=Roboto:ital,wght@0,300;0,400;0,500;1,400&display=swap" rel="stylesheet">
<style>
:root{
  --page:#ebebeb;
  --header:#f8f8f8;
  --line:#dcdcdc;
  --text:#444;
  --muted:#666;
  --blue:#2a9bd0;
  --orange:#f0950a;
  --footer:#1e89b6;
  --white:#fff;
}
*{box-sizing:border-box;margin:0;padding:0}
html,body{width:1200px;height:1120px;overflow:hidden}
body{position:relative;background:var(--page);font-family:'Roboto',sans-serif;color:var(--text)}
.abs{position:absolute}
.topbar{left:0;top:0;width:1200px;height:70px;background:var(--header);border-bottom:1px solid var(--line)}
.menu-btn{left:0;top:0;width:145px;height:70px;border-right:1px solid #e6e6e6}
.menu-btn svg{position:absolute;left:101px;top:29px}
.brand{left:167px;top:15px;display:flex;align-items:center;gap:10px}
.brand-dot{width:40px;height:40px;border-radius:50%;background:var(--orange)}
.brand-name{font-size:31px;font-weight:400;color:var(--blue)}
.user{left:746px;top:18px;display:flex;align-items:center;gap:12px;font-size:17px;color:#555;font-weight:300}
.user-avatar{width:34px;height:34px;border-radius:50%;background:linear-gradient(135deg,#6b5b55,#2d2a2a)}
.tool{top:0;height:70px;border-left:1px solid #e6e6e6}
.badge{position:absolute;top:16px;min-width:22px;height:16px;border-radius:8px;color:#fff;font-size:11px;text-align:center;line-height:16px}
.panel{left:99px;top:111px;width:1001px;height:822px;background:var(--white);border:1px solid #e0e0e0;overflow:hidden}
.panel-head{left:0;top:0;width:999px;height:48px;background:#f5f6f8;border-bottom:1px solid #e0e0e0;font-size:15px;color:#555;padding:18px 19px;letter-spacing:.1px}
.field-label{font-size:14px;color:#666;font-weight:300}
.input{background:#fff;border:1px solid #e2e2e2;box-shadow:0 1px 2px rgba(0,0,0,.04);font-size:13px;color:#555;padding:0 22px;display:flex;align-items:center}
.select-arrow{position:absolute;right:0;top:0;width:38px;height:100%;border-left:1px solid #e2e2e2;display:flex;align-items:center;justify-content:center}
.group-photo{border-radius:50%}
.group-title{font-size:15px;color:var(--blue);font-weight:300}
.group-desc{font-size:11px;font-style:italic;color:#555;line-height:19px}
.member-photo{width:57px;height:57px;border-radius:50%}
.member-name{font-size:15px;color:#333;font-weight:300}
.save{width:122px;height:36px;background:var(--orange);color:#fff;font-size:15px;font-weight:500;text-align:center;line-height:36px;border-bottom:2px solid #d27f05}
.deco{left:685px;top:86px;width:283px;height:240px;border-radius:50%;background:radial-gradient(ellipse at 45% 45%,#fffcf5 0%,#fdfcf8 55%,#fafbfd 100%)}
.footer{left:0;top:973px;width:1200px;height:147px;background:var(--footer);color:#fff;text-align:center}
.social{display:flex;justify-content:center;gap:13px;margin-top:27px}
.social span{width:24px;height:24px;background:#fff;border-radius:3px}
.links{margin-top:15px;font-size:14px;font-weight:300;word-spacing:2px}
.links i{font-style:normal;margin:0 9px}
.copy{margin-top:12px;font-size:14px}
</style>
</head>
<body>
<header class="abs topbar">
  <div class="abs menu-btn"><svg width="18" height="16"><rect y="1" width="18" height="3" fill="#888"/><rect y="7" width="18" height="3" fill="#888"/><rect y="13" width="18" height="3" fill="#888"/></svg></div>
  <div class="abs brand"><span class="brand-dot"></span><span class="brand-name">Teamora</span></div>
  <div class="abs user"><span class="user-avatar" role="img" aria-label="User profile photo"></span>Daniel Reeve
    <svg width="12" height="8"><path d="M0 0h12L6 7z" fill="#555"/></svg></div>
  <div class="abs tool" style="left:922px;width:69px">
    <svg class="abs" style="left:24px;top:26px" width="20" height="18"><rect width="20" height="4" fill="#666"/><rect y="7" width="12" height="4" fill="#666"/><rect y="14" width="20" height="4" fill="#666"/></svg>
    <span class="badge" style="left:35px;background:var(--orange)">8</span>
  </div>
  <div class="abs tool" style="left:991px;width:60px">
    <svg class="abs" style="left:20px;top:26px" width="20" height="20"><circle cx="8" cy="8" r="6" stroke="#666" stroke-width="2.5" fill="none"/><path d="M12.5 12.5l5 5" stroke="#666" stroke-width="3"/></svg>
  </div>
  <div class="abs tool" style="left:1051px;width:149px">
    <svg class="abs" style="left:20px;top:26px" width="18" height="20"><path d="M9 1c-4 0-6 3-6 7v5l-2 3h16l-2-3V8c0-4-2-7-6-7zM7 17h4a2 2 0 0 1-4 0z" fill="#666"/></svg>
    <span class="badge" style="left:27px;background:var(--blue)">8</span>
  </div>
</header>

<main class="abs panel">
  <div class="abs panel-head">CREATE NEW BUSINESS OPPORTUNITY - STEP 3
    <svg class="abs" style="right:30px;top:20px" width="7" height="11"><path d="M1 1l4 4.5L1 10" stroke="#aaa" stroke-width="2" fill="none"/></svg>
  </div>
  <div class="abs deco" role="img" aria-label="Faint background decoration"></div>

  <label class="abs field-label" style="left:32px;top:89px">Add Member : *</label>
  <div class="abs input" style="left:205px;top:79px;width:468px;height:39px"></div>

  <label class="abs field-label" style="left:32px;top:143px">Choose Group : *</label>
  <div class="abs input" style="left:205px;top:133px;width:468px;height:39px">Create Group
    <span class="select-arrow"><svg width="10" height="6"><path d="M1 1l4 4 4-4" stroke="#666" stroke-width="1.3" fill="none"/></svg></span></div>
  <div class="abs input" style="left:205px;top:179px;width:468px;height:39px">Enter the new Group name</div>

  <div class="abs group-photo" style="left:205px;top:246px;width:68px;height:68px;background:linear-gradient(135deg,#a88a6a,#2f3640)" role="img" aria-label="Administrators group photo"></div>
  <div class="abs group-title" style="left:291px;top:246px">Administrators</div>
  <div class="abs group-desc" style="left:291px;top:272px">Lorem ipsum dolor sit amet,<br>consectetur adipiscing elit, sed do</div>
  <svg class="abs" style="left:644px;top:250px" width="12" height="12"><path d="M1 1l5 5 5-5M1 6l5 5 5-5" stroke="#555" stroke-width="1.4" fill="none"/></svg>

  <div class="abs member-photo" style="left:276px;top:329px;background:linear-gradient(135deg,#c79a7a,#7a5b4a)" role="img" aria-label="Member photo"></div>
  <div class="abs member-name" style="left:349px;top:349px">Lina Farouk</div>
  <div class="abs member-photo" style="left:276px;top:398px;background:linear-gradient(135deg,#e5e5e5,#2b3444)" role="img" aria-label="Member photo"></div>
  <div class="abs member-name" style="left:349px;top:418px">Karim Nadeem</div>
  <div class="abs member-photo" style="left:276px;top:468px;background:linear-gradient(135deg,#b7c4d0,#8a6a55)" role="img" aria-label="Member photo"></div>
  <div class="abs member-name" style="left:349px;top:488px">Omar Tarek</div>

  <div class="abs group-photo" style="left:205px;top:555px;width:68px;height:68px;background:linear-gradient(135deg,#8fb5d6,#5c8a4a)" role="img" aria-label="Buyers group photo"></div>
  <div class="abs group-title" style="left:291px;top:555px">Buyers</div>
  <div class="abs group-desc" style="left:291px;top:580px">Lorem ipsum dolor sit amet,<br>consectetur adipiscing elit, sed do</div>
  <svg class="abs" style="left:644px;top:594px" width="12" height="12"><path d="M1 6l5-5 5 5M1 11l5-5 5 5" stroke="#555" stroke-width="1.4" fill="none"/></svg>

  <div class="abs group-photo" style="left:205px;top:649px;width:68px;height:68px;background:linear-gradient(135deg,#e0dcd4,#3c4048)" role="img" aria-label="Sellers group photo"></div>
  <div class="abs group-title" style="left:291px;top:649px">Sellers</div>
  <div class="abs group-desc" style="left:291px;top:674px">Lorem ipsum dolor sit amet,<br>consectetur adipiscing elit, sed do</div>
  <svg class="abs" style="left:644px;top:688px" width="12" height="12"><path d="M1 6l5-5 5 5M1 11l5-5 5 5" stroke="#555" stroke-width="1.4" fill="none"/></svg>

  <div class="abs save" style="left:207px;top:750px">SAVE</div>
</main>

<footer class="abs footer">
  <div class="social"><span></span><span></span><span></span><span></span><span></span></div>
  <nav class="links">Home<i>/</i>Contact<i>/</i>Topics<i>/</i>Posts and Comments<i>/</i>Discussion<i>/</i>Videos Links</nav>
  <div class="copy">Copyright @ 2015 - 2015.Teamora. All Rights Reserved.</div>
</footer>
</body>
</html>
```